Business card for a new innovative and professional lawn care business

We need a business card design for a new lawn care business in Halifax NS Canada. We offer lawn services in Halifax & Bedford. Our services offered include lawn care, garden services, and property maintenance. We take pride in our work and are experienced at what we do. I would like to see a design that is double sided. On the backside I would like the something simple (maybe my logo preferably on blackround (linked below) with website link, Facebook page or something). The front I want to include contact info:
Morgan Pell
phone 902-555-0148
email - brookvaleyards.ca
facebook - Facebook.com/brookvaleyards
Instagram maybe ? - instagram.com/brookvaleyard
Serving Halifax and Bedford for 5 years?
I don't want it to have too much information as I will be passing them out in aim to visit website, or call !
We do want it to include lawn care, garden services and property maintenance.
Basic, catchy, and modern looking !
Logo attached below !

Target Market(s)

Passing business cards to everyone I meet or interact with.

Industry/Entity Type

Lawn Care

Contact Information for Business Card

Double sided with some basic information, with catchy colours and easy to look at.

Font styles to use
Sans Serif

Requirements
Must have
• Must be double sided and have :
• Name, Phone, Email, FB, Website, and 3 main services offered - lawn care, property maintenance, garden services
Nice to have
• Would be nice to have instagram link if it goes well on there
Should not have
• Don't want too much writing or images that are distracting

```html
<!DOCTYPE html>
<html lang="en">
<head>
<meta charset="utf-8">
<title>Brookvale Yards – Business Card</title>
<link href="https://fonts.googleapis.com/css2?family=Open+Sans:wght@400;600;700&display=swap" rel="stylesheet">
<style>
  :root {
    --page-bg: #e9eaea;
    --card-white: #ffffff;
    --brand-green: #006b3a;
    --name-green: #0b6b35;
    --logo-green: #2f9a3a;
    --text-grey: #4a4a4a;
    --rule-grey: #cfcfcf;
    --white: #ffffff;
  }
  * { margin: 0; padding: 0; box-sizing: border-box; }
  html, body {
    width: 1105px; height: 1200px; overflow: hidden;
    background: var(--page-bg);
    font-family: "Open Sans", Arial, sans-serif;
  }
  .canvas { position: relative; width: 1105px; height: 1200px; }
  .card {
    position: absolute; left: 192px; width: 720px; height: 410px;
  }
  .card-front { top: 146px; background: var(--card-white); }
  .card-back { top: 602px; background: var(--brand-green); }

  .brand-mark {
    position: absolute; display: flex; align-items: center; gap: 12px;
    font-weight: 700; white-space: nowrap;
  }
  .card-front .brand-mark {
    left: 56px; top: 183px; font-size: 33px; color: var(--logo-green);
  }
  .brand-dot {
    width: 22px; height: 22px; border-radius: 50%; background: currentColor; flex: none;
  }
  .divider {
    position: absolute; left: 391px; top: 102px; width: 1px; height: 208px;
    background: var(--rule-grey);
  }
  .contact-block { position: absolute; left: 420px; top: 112px; }
  .contact-name {
    font-size: 26px; font-weight: 600; color: var(--name-green); line-height: 1.2;
    margin-bottom: 12px;
  }
  .contact-list { list-style: none; }
  .contact-item {
    display: flex; align-items: center; gap: 10px;
    font-size: 18.5px; color: var(--text-grey); height: 28px;
  }
  .contact-icon { width: 16px; height: 16px; flex: none; }
  .social-square {
    width: 15px; height: 15px; background: var(--name-green); border-radius: 2px; flex: none;
  }

  .card-back .brand-mark {
    left: 0; right: 0; top: 158px; justify-content: center;
    font-size: 44px; color: var(--white);
  }
  .card-back .brand-dot { width: 28px; height: 28px; }
  .service-line {
    position: absolute; left: 0; right: 0; top: 343px;
    display: flex; justify-content: center; align-items: center; gap: 12px;
    font-size: 19px; color: var(--white);
  }
  .service-sep {
    width: 8px; height: 8px; border-radius: 50%; background: var(--white);
  }
</style>
</head>
<body>
<main class="canvas">
  <section class="card card-front" aria-label="Card front">
    <div class="brand-mark"><span class="brand-dot"></span>Brookvale Yards</div>
    <div class="divider"></div>
    <div class="contact-block">
      <h1 class="contact-name">Morgan Pell</h1>
      <ul class="contact-list">
        <li class="contact-item">
          <svg class="contact-icon" viewBox="0 0 16 16" aria-hidden="true"><path fill="#0b6b35" d="M3.5 1.5l2.6 2.4-1.3 2.2c.9 2 2.5 3.6 4.5 4.5l2.2-1.3 2.4 2.6-1.6 2c-5.6-.4-10.4-5.2-10.8-10.8z"/></svg>
          902-555-0148
        </li>
        <li class="contact-item">
          <svg class="contact-icon" viewBox="0 0 16 16" aria-hidden="true"><rect x="1" y="3" width="14" height="10" fill="#0b6b35"/><path d="M1.5 3.5L8 9l6.5-5.5" fill="none" stroke="#fff" stroke-width="1.3"/></svg>
          info@brookvaleyards.ca
        </li>
        <li class="contact-item">
          <svg class="contact-icon" viewBox="0 0 16 16" aria-hidden="true"><circle cx="8" cy="8" r="7" fill="#0b6b35"/><path d="M1 8h14M8 1c-3 3.5-3 10.5 0 14M8 1c3 3.5 3 10.5 0 14" fill="none" stroke="#fff" stroke-width="1"/></svg>
          brookvaleyards.ca
        </li>
        <li class="contact-item"><span class="social-square"></span>brookvaleyards</li>
        <li class="contact-item"><span class="social-square"></span>brookvaleyard</li>
      </ul>
    </div>
  </section>

  <section class="card card-back" aria-label="Card back">
    <div class="brand-mark"><span class="brand-dot"></span>Brookvale Yards</div>
    <p class="service-line">
      <span>Lawn Care</span><span class="service-sep"></span>
      <span>Property Maintenance</span><span class="service-sep"></span>
      <span>Garden Services</span>
    </p>
  </section>
</main>
</body>
</html>
```